Single-sided business card for restaurant velmora with new logo made on this site

Business card options with new logo including restaurant name, address, phone number and website. This business card is single-sided only and will be presented at the hostess desk for clients to take. I would like to see options based on a cream card background, a white card background, a yellow card background and a burgundy colored background. It needs to be elegant and traditional.

Target Market(s)

local and international crowd

Industry/Entity Type

restaurant

Contact Information for Business Card

address, website and phone number

Font styles to use
Serif

Colors
EE7325
F08F49
F5BC92
FAE3D3
FDF4ED

Requirements
Must have
• new logo, address, phone number, website
Should not have
• more than three colors

```html
<!DOCTYPE html>
<html lang="es">
<head>
<meta charset="utf-8">
<title>Velmora – Tarjeta de presentación</title>
<link href="https://fonts.googleapis.com/css2?family=Cinzel:wght@500;600&display=swap" rel="stylesheet">
<style>
  :root {
    --backdrop: #8c8c8c;
    --card: #ecebec;
    --gold: #e4a42c;
    --ink: #2b1417;
  }
  html, body {
    margin: 0;
    width: 1200px;
    height: 1101px;
    overflow: hidden;
    background: var(--backdrop);
  }
  .business-card {
    position: absolute;
    left: 100px;
    top: 267px;
    width: 1000px;
    height: 566px;
    background: var(--card);
    font-family: "Cinzel", "Times New Roman", serif;
    color: var(--ink);
  }
  .card-frame {
    position: absolute;
    inset: 32px;
    border: 2px solid var(--gold);
  }
  .brand {
    position: absolute;
    left: 97px;
    top: 160px;
    width: 300px;
    text-align: center;
  }
  .brand-square {
    display: block;
    width: 141px;
    height: 141px;
    margin: 0 auto 22px;
    background: var(--gold);
  }
  .brand-name {
    margin: 0;
    font-size: 44px;
    font-weight: 600;
    letter-spacing: 6px;
    line-height: 1;
  }
  .divider {
    position: absolute;
    left: 474px;
    top: 113px;
    width: 3px;
    height: 340px;
    background: var(--gold);
  }
  .contact {
    position: absolute;
    left: 550px;
    top: 122px;
    margin: 0;
    font-size: 27px;
    font-weight: 600;
    line-height: 40px;
    font-style: normal;
  }
  .contact p { margin: 0; }
  .contact .address { margin-bottom: 40px; }
</style>
</head>
<body>
  <main class="business-card">
    <div class="card-frame"></div>

    <div class="brand">
      <span class="brand-square"></span>
      <h1 class="brand-name">VELMORA</h1>
    </div>

    <div class="divider"></div>

    <address class="contact">
      <p class="address">Restaurant Velmora<br>Jacaranda 415<br>Bahía Serena,<br>Oaxaca CP 70412</p>
      <p class="reservations">Reservaciones<br>958-214-3370<br>www.velmora.com.mx</p>
    </address>
  </main>
</body>
</html>
```